Talvique Hotels Business Card and Logo

We need a business card design for a hotel group. I saw a hotel card you designed and really liked it. We have multiple properties with different brands. Were hoping that the card would be unique and find a way to list out all our properties. Our web address is www.talviquehotels.com. I have attached some photos of card designs I like.

Industry/Entity Type

Hotel

Contact Information for Business Card

Scott CurranReneson HotelsChief Operating Officer56 Madera DriveCorte Madera, CA 94925Office 415-891-5013Cell 707-5550143

```html
<!DOCTYPE html>
<html lang="en">
<head>
<meta charset="utf-8">
<title>Talvique Hotels Business Card</title>
<link rel="stylesheet" href="https://fonts.googleapis.com/css2?family=Montserrat:wght@400;500;600&family=Roboto:wght@500&display=swap">
<style>
  :root {
    --backdrop: #2b2b2b;
    --paper: #ffffff;
    --navy: #0d3b66;
    --green: #7cb342;
    --ink: #3d3d3d;
    --photo-top: #3c6a8c;
    --photo-mid: #2f6f8f;
    --photo-bottom: #1f7ea6;
  }
  * { margin: 0; padding: 0; box-sizing: border-box; }
  html, body { width: 1200px; height: 900px; overflow: hidden; }
  body { background: var(--backdrop); position: relative; font-family: "Montserrat", sans-serif; }

  .card { position: absolute; left: 261px; width: 656px; height: 358px; overflow: hidden; }
  .card-front { top: 69px; background: var(--paper); }
  .card-back { top: 472px; }

  .wordmark {
    position: absolute; left: 27px; top: 24px;
    font-family: "Montserrat", sans-serif; font-weight: 600;
    font-size: 24px; letter-spacing: 2.5px; color: var(--navy);
    text-transform: uppercase; line-height: 1;
  }

  .holder { position: absolute; right: 30px; top: 154px; text-align: right; }
  .holder-name {
    font-family: "Roboto", sans-serif; font-weight: 500;
    font-size: 24px; color: var(--navy); line-height: 28px;
  }
  .holder-title {
    font-size: 14.5px; letter-spacing: 1px; color: var(--ink); line-height: 18px;
  }

  .divider { position: absolute; left: 27px; width: 599px; top: 213px; height: 1px; background: var(--green); }

  .contact-list { position: absolute; left: 27px; top: 238px; list-style: none; }
  .contact-list li {
    display: flex; align-items: center; gap: 8px;
    font-size: 16px; letter-spacing: 1px; color: var(--ink); height: 21px;
  }
  .contact-list svg { width: 11px; height: 11px; flex: none; }

  .address {
    position: absolute; right: 29px; top: 280px; text-align: right;
    font-size: 16px; letter-spacing: 1px; color: var(--ink); line-height: 21px;
  }

  .corner-bands { position: absolute; left: 0; bottom: 0; width: 656px; height: 28px; }

  .back-photo {
    position: absolute; inset: 0;
    background: linear-gradient(180deg, var(--photo-top) 0%, var(--photo-mid) 55%, var(--photo-bottom) 100%);
  }
  .back-wordmark {
    position: absolute; left: 0; right: 0; top: 160px; text-align: center;
    font-family: "Montserrat", sans-serif; font-weight: 600;
    font-size: 40px; letter-spacing: 4px; color: var(--paper);
    text-transform: uppercase; line-height: 1;
  }
</style>
</head>
<body>
  <section class="card card-front">
    <div class="wordmark">Talvique Hotels</div>

    <div class="holder">
      <div class="holder-name">Brent Holloway Talvique</div>
      <div class="holder-title">Hotels Chief Operating Officer</div>
    </div>

    <div class="divider"></div>

    <ul class="contact-list">
      <li>
        <svg viewBox="0 0 12 12"><path d="M3 1 L5 3.5 L4 5 Q5 7 7 8 L8.5 7 L11 9 L9.5 11 Q5 10.5 1.5 5 Q1 3 3 1 Z" fill="var(--green)"/></svg>
        415-555-0186
      </li>
      <li>
        <svg viewBox="0 0 12 12"><rect x="3" y="1" width="6" height="10" rx="1" fill="none" stroke="var(--green)" stroke-width="1.4"/><rect x="4.5" y="2.5" width="3" height="5" fill="var(--green)"/></svg>
        707-5550143
      </li>
      <li>
        <svg viewBox="0 0 12 12"><rect x="1" y="3" width="10" height="7" fill="none" stroke="var(--green)" stroke-width="1.2"/><path d="M1 3 L6 7 L11 3" fill="none" stroke="var(--green)" stroke-width="1.2"/></svg>
        info@talviquehotels.com
      </li>
      <li>
        <svg viewBox="0 0 12 12"><circle cx="6" cy="6" r="5" fill="none" stroke="var(--green)" stroke-width="1"/><ellipse cx="6" cy="6" rx="2.2" ry="5" fill="none" stroke="var(--green)" stroke-width="1"/><path d="M1 6 H11 M2 3.5 H10 M2 8.5 H10" stroke="var(--green)" stroke-width="0.8"/></svg>
        www.talviquehotels.com
      </li>
    </ul>

    <div class="address">
      <div>83 Pellwick Lane</div>
      <div>Marlow Bay, CA 94931</div>
    </div>

    <svg class="corner-bands" viewBox="0 0 656 28" preserveAspectRatio="none">
      <polygon points="0,17 356,17 346,28 0,28" fill="var(--green)"/>
      <polygon points="381,0 656,0 656,28 353,28" fill="var(--navy)"/>
    </svg>
  </section>

  <section class="card card-back">
    <div class="back-photo" role="img" aria-label="Photo of a hotel pool courtyard with lounge chairs, umbrellas and a two-storey building under a blue tint"></div>
    <div class="back-wordmark">Talvique Hotels</div>
  </section>
</body>
</html>
```